BRANDEMEIER & BRANDEMEIER,LLP NEEDS A NEW LETTERHEAD DESIGN

a conservative yet contemporary layout befitting a long established
firm, consistent with the times, some form of logo so it catches ones attention, and is
admirable, but portrays integrity
Updates

I would like to approve #22066987 Please advise how to do this as it’s confusing on the site so I can approve payment for the designer

Target Market(s)

real estate investors and building management people

Industry/Entity Type

Law Firm

Font styles to use
Serif

Colors

Designer to choose colors to be used in the design.

Requirements
Must have
• some form of conservative logo

```html
<!DOCTYPE html>
<html lang="en">
<head>
<meta charset="utf-8">
<title>Brandemeier &amp; Brandemeier, LLP — Letterhead</title>
<link rel="stylesheet" href="https://fonts.googleapis.com/css2?family=Cinzel:wght@400;500&family=Arimo:wght@400&display=swap">
<style>
  :root {
    --backdrop: #c9cace;
    --paper: #f1f1f1;
    --ink-dark: #2b2d33;
    --ink-mid: #4a4c52;
    --ink-soft: #6b6d72;
    --mark-grey: #b3b4b7;
    --watermark: #e6e6e8;
    --rule: #c4c5c8;
  }
  html, body {
    margin: 0;
    padding: 0;
    width: 1200px;
    height: 1166px;
    overflow: hidden;
    background: var(--backdrop);
  }
  .letterhead {
    position: absolute;
    left: 214px;
    top: 69px;
    width: 788px;
    height: 1019px;
    background: var(--paper);
    overflow: hidden;
  }
  .brand-dot {
    position: absolute;
    left: 50%;
    top: 54px;
    width: 50px;
    height: 50px;
    margin-left: -25px;
    border: 1.5px solid var(--mark-grey);
    border-radius: 50%;
    box-sizing: border-box;
  }
  .firm-name {
    position: absolute;
    top: 131px;
    left: 0;
    width: 100%;
    margin: 0;
    text-align: center;
    font-family: "Cinzel", serif;
    font-weight: 500;
    font-size: 17px;
    line-height: 22px;
    letter-spacing: 0.2px;
    color: var(--ink-dark);
  }
  .firm-tagline {
    position: absolute;
    top: 157px;
    left: 0;
    width: 100%;
    margin: 0;
    text-align: center;
    font-family: "Cinzel", serif;
    font-size: 10.5px;
    line-height: 14px;
    letter-spacing: 0.4px;
    color: var(--ink-mid);
  }
  .watermark-name {
    position: absolute;
    left: 0;
    top: 389px;
    width: 100%;
    margin: 0;
    text-align: center;
    font-family: "Cinzel", serif;
    font-weight: 400;
    font-size: 60px;
    line-height: 80px;
    color: var(--watermark);
  }
  .footer {
    position: absolute;
    left: 0;
    top: 922px;
    width: 100%;
    text-align: center;
    font-family: "Arimo", sans-serif;
  }
  .footer-web {
    margin: 0;
    font-size: 10px;
    line-height: 14px;
    letter-spacing: 4.5px;
    color: var(--ink-soft);
  }
  .footer-rule {
    width: 452px;
    height: 0;
    margin: 12px auto 6px;
    border: 0;
    border-top: 1px solid var(--rule);
  }
  .footer-contact {
    margin: 0;
    font-size: 9.5px;
    line-height: 12.5px;
    color: var(--ink-soft);
  }
</style>
</head>
<body>
  <main class="letterhead">
    <div class="brand-dot" aria-hidden="true"></div>
    <h1 class="firm-name">BRANDEMEIER &amp; BRANDEMEIER, LLP</h1>
    <p class="firm-tagline">Attorneys and Counselors at Law</p>

    <p class="watermark-name" aria-hidden="true">BRANDEMEIER<br>&amp;<br>BRANDEMEIER</p>

    <footer class="footer">
      <p class="footer-web">www.bbrelaw.com</p>
      <hr class="footer-rule">
      <p class="footer-contact">Brandemeier &amp; Brandemeier, LLP · 48 Harbor Street Suite 210, Brooklyn, New York 11201<br>
      Phone: (718) 555-0142 · Fax: (718)-555-0179 · Email: info@bbrelaw.com</p>
    </footer>
  </main>
</body>
</html>
```